Hollow Thicket, a 3d voxel survival video game needs a card for gaming conventions

I am the lead developer for Hollow Thicket http://www.HollowThicket.example and need a business card to hand out at an indie gaming convention
The card would need to include the game name, website url, my name, position (Lead Developer), e-mail and phone number
The game is a 3d, voxel (with smooth terrain) based survival game with guns and wildlife. The main icon of the game would likely be a grizzly bear but I am willing to accept other designs too.
Attached is a media kit for the game with some images you can use but don't have to its just what little art I can provide. Anything on the website or from the video game can also be used. unrelated art can also be used.
Target Market(s)
Indie Developers/publishers at conferences
Industry/Entity Type
Games
Contact Information for Business Card
Name: Corin Waldrick
Position: Lead Developer
E-mail: Pale_Kettle@mailbox.example
Phone number: 555-372-1186

```html
<!DOCTYPE html>
<html lang="en">
<head>
<meta charset="utf-8">
<title>Hollow Thicket – Business Card</title>
<link rel="stylesheet" href="https://fonts.googleapis.com/css2?family=Open+Sans:wght@400;600;700&display=swap">
<style>
  :root {
    --bg: #ece8e2;
    --card: #ffffff;
    --red: #a3161a;
    --gold: #a88d55;
    --gold-light: #b89d66;
    --ink: #333333;
    --logo: #7e1a17;
    --photo-sky: #e9eef2;
    --photo-field: #d98a3a;
    --photo-bear: #6b4029;
  }
  * { margin: 0; padding: 0; box-sizing: border-box; }
  html, body { width: 1200px; height: 900px; overflow: hidden; }
  body {
    background: var(--bg);
    font-family: "Open Sans", Arial, sans-serif;
    position: relative;
  }
  .card {
    position: absolute;
    left: 337px;
    width: 525px;
    height: 300px;
    background: var(--card);
    overflow: hidden;
    box-shadow: 0 6px 18px rgba(0,0,0,0.18);
  }
  .card--front { top: 120px; }
  .card--back { top: 480px; }

  .front-photo {
    position: absolute; inset: 0;
    background:
      radial-gradient(ellipse 55% 70% at 68% 50%, var(--photo-bear) 0%, rgba(107,64,41,0.85) 45%, rgba(107,64,41,0) 75%),
      linear-gradient(180deg, var(--photo-sky) 0%, #e8c89a 28%, var(--photo-field) 50%, #c9742e 100%);
  }
  .front-logo {
    position: absolute;
    left: 0; right: 0; top: 128px;
    text-align: center;
    font-weight: 700;
    font-size: 38px;
    letter-spacing: 3px;
    text-transform: uppercase;
    color: #ffffff;
  }

  .holder {
    position: absolute; left: 34px; top: 40px;
  }
  .holder-name {
    font-weight: 600;
    font-size: 17px;
    text-transform: uppercase;
    letter-spacing: 0.3px;
  }
  .holder-name .first { color: var(--red); }
  .holder-name .last { color: var(--gold); }
  .holder-role {
    font-size: 13px;
    color: var(--ink);
    margin-top: 2px;
  }
  .back-logo {
    position: absolute; right: 30px; top: 78px;
    font-weight: 700;
    font-size: 27px;
    letter-spacing: 2px;
    text-transform: uppercase;
    color: var(--logo);
  }
  .contact {
    position: absolute; left: 40px; top: 150px;
    list-style: none;
    font-size: 14px;
    color: var(--ink);
  }
  .contact li { display: flex; align-items: center; gap: 8px; line-height: 22px; white-space: nowrap; }
  .contact svg { width: 12px; height: 12px; flex: none; }
  .swoosh { position: absolute; left: 0; bottom: 0; width: 525px; height: 300px; }
</style>
</head>
<body>

  <section class="card card--front">
    <div class="front-photo" role="img" aria-label="Photograph of a roaring grizzly bear in an autumn field"></div>
    <div class="front-logo">Hollow Thicket</div>
  </section>

  <section class="card card--back">
    <svg class="swoosh" viewBox="0 0 525 300" aria-hidden="true">
      <defs>
        <linearGradient id="redBand" x1="0" y1="1" x2="1" y2="0">
          <stop offset="0" stop-color="#a3161a"/>
          <stop offset="1" stop-color="#c0623c"/>
        </linearGradient>
      </defs>
      <path d="M0,240 C150,300 330,190 525,130 L525,300 L0,300 Z" fill="#b89d66"/>
      <path d="M0,258 C160,306 340,212 525,172 L525,300 L0,300 Z" fill="#ffffff"/>
      <path d="M0,266 C160,312 340,224 525,186 L525,300 L0,300 Z" fill="url(#redBand)"/>
    </svg>

    <div class="holder">
      <p class="holder-name"><span class="first">Corin</span> <span class="last">Waldrick</span></p>
      <p class="holder-role">Lead Developer</p>
    </div>

    <div class="back-logo">Hollow Thicket</div>

    <ul class="contact">
      <li>
        <svg viewBox="0 0 12 12" aria-hidden="true"><path d="M1,5 Q6,1 11,5 L10,6.5 L8,5.5 L8,4.5 Q6,3.8 4,4.5 L4,5.5 L2,6.5 Z M3,7 L9,7 L10,11 L2,11 Z" fill="#a3161a"/></svg>
        555-372-1186
      </li>
      <li>
        <svg viewBox="0 0 12 12" aria-hidden="true"><rect x="0.5" y="2.5" width="11" height="7" fill="#a3161a"/><path d="M0.5,2.5 L6,7 L11.5,2.5" fill="none" stroke="#ffffff" stroke-width="1"/></svg>
        Pale_Kettle@mailbox.example
      </li>
      <li>
        <svg viewBox="0 0 12 12" aria-hidden="true"><circle cx="6" cy="6" r="5" fill="none" stroke="#a3161a" stroke-width="1.3"/><ellipse cx="6" cy="6" rx="2.2" ry="5" fill="none" stroke="#a3161a" stroke-width="1"/><line x1="1" y1="6" x2="11" y2="6" stroke="#a3161a" stroke-width="1"/></svg>
        http://www.HollowThicket.example
      </li>
    </ul>
  </section>

</body>
</html>
```